WordPress Website for BidLinks Agency

We are in need of a complete WordPress design.

We will be seeking new clients and we want them to have a great idea of what our business does when they get to the page along with the products and services we offer. Our current website is www.mossyharbor.com and it really needs an upgrade. Wordpress would be great but our owner knows HTML as well so he can go in and edit things later if need be. Please apply if you can show what a Search Engine Marketing company does and can explain this information to a lay person. Also, the website should be responsive so it fits mobile, tablet, and desktop settings while changing to these different widths.

Also, we are not an SEO company, per se but an SEM / PPC company that operates on Zorvic BidLinks, Plim Promos, Chatterwall Promos, and other PPC platforms.

Themes are fine just as long as the content and the visuals display what a search engine marketing company does. Really looking for clients to know exactly why a search engine marketing company does when the get to the site, why they should use a search engine marketing company, and the best way to contact us to get a quote.

Here are some other search engine marketing sites that I like in terms of the content and the layout to give an idea of what should be included on the site:
http://www.fendowlabs.com/
http://www.k9rworks.com/
http://www.boulderpartners.com/
http://www.vjnpromo.com/
http://www.halvorteam.com/
http://meetthepinecrew.com/

Please include my new phone number of the website: 866-555-0142.

Thank you, 
Walt 

Target Market(s)

We are a search engine marketing company looking for more clients and want to be able to explain what a search engine marketing company does in layman's terms.

Industry/Entity Type

Marketing

Font styles to use
Sans Serif

Requirements
Must have
• About Us Page
Services Page
Home Page
Success Stories Page
Blog
Social Media links / feeds
Visuals of products / services offered
Jobs page
Nice to have
• Responsive design
Client Login / Space on the site for monthly client payments / Link to CoinTap or Rivermoss

```html
<!DOCTYPE html>
<html lang="en">
<head>
<meta charset="utf-8">
<title>Mossy Harbor Digital Marketing</title>
<link rel="stylesheet" href="https://fonts.googleapis.com/css2?family=Oswald:wght@400;500&family=Ubuntu:wght@300;400;500&display=swap">
<style>
:root{
  --red:#e8262b;
  --red-band:#ef3b3e;
  --green:#5fb322;
  --ink:#2d2d2d;
  --muted:#555;
  --panel:#f1f1f1;
  --rule:#d6d6d6;
  --footer:#3b3b3b;
  --blue:#1f63b5;
  --slide-dark:#0b1626;
  --slide-mid:#1d3a63;
}
*{box-sizing:border-box;margin:0;padding:0}
html,body{width:900px;height:1200px;overflow:hidden}
body{position:relative;background:#fff;font-family:'Ubuntu',sans-serif;color:var(--ink)}
.abs{position:absolute}

/* header */
.site-header{left:0;top:0;width:900px;height:104px;background:linear-gradient(#fbfbfb,#ececec)}
.brand{left:98px;top:34px;display:flex;align-items:center;gap:8px}
.brand-dot{width:22px;height:22px;border-radius:50%;background:var(--red)}
.brand-name{font-weight:500;font-size:24px;color:var(--red);letter-spacing:-.5px}
.search{left:502px;top:20px;width:180px;height:24px;border-radius:12px;background:#fff;border:1px solid #ddd;box-shadow:inset 0 1px 3px rgba(0,0,0,.12)}
.search-btn{position:absolute;right:2px;top:2px;width:18px;height:18px;border-radius:50%;background:#111}
.social{left:692px;top:24px;display:flex;gap:6px}
.social span{width:17px;height:17px;border-radius:50%;background:var(--red);display:block}
.main-nav{right:98px;top:70px;display:flex;gap:17px;font-size:12.5px;color:#444}

/* hero */
.hero-band{left:0;top:104px;width:900px;height:370px;background:linear-gradient(var(--red),var(--red-band))}
.slide-frame{left:97px;top:96px;width:705px;height:328px;background:#fff;padding:4px;box-shadow:0 6px 14px rgba(0,0,0,.35)}
.slide-photo{width:100%;height:100%;background:
  radial-gradient(ellipse 28% 40% at 76% 30%,rgba(120,200,90,.55),transparent 70%),
  radial-gradient(ellipse 22% 30% at 88% 22%,rgba(190,90,210,.55),transparent 70%),
  radial-gradient(ellipse 20% 30% at 62% 62%,rgba(240,150,50,.45),transparent 70%),
  radial-gradient(ellipse 30% 30% at 40% 60%,rgba(150,150,170,.35),transparent 70%),
  linear-gradient(0deg,rgba(70,140,230,.55) 0%,transparent 35%),
  radial-gradient(circle at 70% 40%,#2d5c94 0%,var(--slide-mid) 35%,var(--slide-dark) 85%)}
.slide-copy{left:131px;top:150px;font-family:'Oswald',sans-serif;line-height:1}
.slide-kicker{font-size:31px;color:var(--red);font-weight:500}
.slide-title{font-size:46px;color:#fff;margin-top:2px}
.slide-sub{font-size:22px;color:#fff;margin-top:4px}
.slide-cta{left:130px;top:270px;width:181px;height:32px;background:var(--green);color:#fff;font-family:'Oswald',sans-serif;font-size:16px;display:flex;align-items:center;justify-content:center}
.slide-dots{left:410px;top:441px;width:80px;height:23px;border-radius:12px;background:#111;display:flex;align-items:center;justify-content:center;gap:5px}
.slide-dots span{width:9px;height:9px;border-radius:50%;background:#bbb}
.slide-dots span.on{background:#fff}

/* welcome */
.welcome{left:97px;top:500px;width:705px;text-align:center}
.welcome h1{font-weight:400;font-size:19px;color:#222}
.welcome p{margin-top:14px;font-size:10.3px;line-height:17.4px;color:var(--muted);font-weight:300}
.divider{left:97px;top:608px;width:705px;height:1px;background:var(--rule)}

/* products */
.section-title{font-weight:400;font-size:18.5px;color:#222}
.products-title{left:97px;top:624px}
.thumb{width:162px;height:91px;background:#fff;border:1px solid #ddd;padding:4px;box-shadow:0 1px 3px rgba(0,0,0,.15)}
.thumb div{width:100%;height:100%}
.t1{background:radial-gradient(ellipse 40% 45% at 50% 60%,rgba(120,200,140,.6),transparent 70%),linear-gradient(90deg,#999,#222 30%,#222 70%,#999)}
.t2{background:radial-gradient(circle at 50% 55%,#4ea3e6,#1a5a9a 40%,#0a1628 80%)}
.t3{background:radial-gradient(ellipse 50% 35% at 65% 60%,rgba(120,210,230,.55),transparent 70%),linear-gradient(135deg,#10151f,#2a3446)}
.t4{background:radial-gradient(circle at 48% 50%,#7ec244 0,#7ec244 10%,#2a6aa8 14%,#174a80 60%,#0e2f56)}
.t5{background:linear-gradient(110deg,#0f3f86 0%,#1e5db0 55%,#c8d8ea 100%)}
.t6{background:radial-gradient(ellipse 35% 45% at 75% 30%,rgba(180,120,220,.55),transparent 70%),linear-gradient(0deg,#3d7fd0 0%,#151b26 45%,#0d0f14)}

.offer-title{left:637px;top:624px}
.offer-list{left:637px;top:654px;list-style:none;font-size:10.4px;color:#444;font-weight:300}
.offer-list li{height:25.5px;display:flex;align-items:center;gap:11px}
.offer-list li::before{content:"";width:8px;height:8px;border-radius:50%;background:var(--red);box-shadow:0 0 0 1px #f7c6c7}

/* panels */
.panel{background:var(--panel);border-radius:3px}
.rss{left:97px;top:868px;width:225px;height:239px;padding:10px 16px}
.panel-head{display:flex;align-items:center;gap:8px;font-size:18px;color:#222}
.rss-item{border-bottom:1px solid #ddd;padding:7px 0 5px;font-size:10.2px;line-height:15px;color:#333}
.rss-item:last-of-type{border-bottom:none}
.rss-date{color:var(--red);font-size:9.6px;margin-top:3px}
.rss-more{text-align:right;color:var(--red);font-weight:500;font-size:9.6px;margin-top:2px}

.vote{left:338px;top:868px;width:225px;height:239px;padding:10px 12px;text-align:center}
.grant-badge{width:140px;height:48px;margin:6px auto 0;background:linear-gradient(90deg,#1f63b5,#2e7fd6);border-radius:3px}
.vote-line{font-family:'Oswald',sans-serif;color:var(--blue);font-weight:400;white-space:nowrap}
.vote-a{font-size:14.5px;margin-top:10px}
.vote-b{font-size:14px;font-weight:500}
.vote-c{font-size:11.5px;margin-top:6px;display:flex;align-items:center;justify-content:center;gap:5px}
.bank{margin-top:10px;display:flex;align-items:center;justify-content:center;gap:6px;font-size:9.5px;font-weight:500;color:#333}
.bank span{width:14px;height:14px;background:var(--blue)}
.vote-btn{margin:10px auto 0;width:66px;height:24px;background:var(--green);color:#fff;font-weight:500;font-size:9.5px;display:flex;align-items:center;justify-content:center}

.cert{left:577px;width:225px;height:112px;padding:10px 12px;display:flex;gap:12px}
.cert-badge{width:70px;height:64px;border:1px solid #ccc;border-radius:3px;background:#e4e4e4;flex:none;margin-top:4px}
.cert h3{font-weight:400;font-size:12px;color:var(--red)}
.cert p{font-size:10px;line-height:15px;color:#444;margin-top:4px;font-weight:300}
.cert-a{top:868px}
.cert-b{top:995px}

/* footer */
.site-footer{left:0;top:1120px;width:900px;height:80px;background:var(--footer)}
.copyright{left:97px;top:1144px;font-size:9.5px;line-height:17px;color:#ddd;font-weight:300}
.badge-a{left:548px;top:1132px;width:85px;height:55px;background:linear-gradient(#777,#444);border:1px solid #888}
.badge-b{left:653px;top:1132px;width:149px;height:55px;background:#0e5d7f;border-radius:6px}
</style>
</head>
<body>

<header class="abs site-header">
  <div class="abs brand"><span class="brand-dot"></span><span class="brand-name">Mossy Harbor</span></div>
  <div class="abs search" role="search" aria-label="Search"><span class="search-btn"></span></div>
  <div class="abs social" aria-label="Social links"><span></span><span></span><span></span><span></span><span></span></div>
  <nav class="abs main-nav"><span>Home</span><span>About us</span><span>Products</span><span>Success stories</span><span>Blog</span><span>Contact us</span></nav>
</header>

<section class="abs hero-band"></section>
<div class="abs slide-frame"><div class="slide-photo" role="img" aria-label="Hand touching a glowing screen as online ad, shopping cart, email and like icons fly out over a city skyline of business people — how search marketing reaches customers"></div></div>
<div class="abs slide-copy">
  <div class="slide-kicker">Mossy Harbor</div>
  <div class="slide-title">Digital Marketing</div>
  <div class="slide-sub">Experts in Explosive Advertising</div>
</div>
<div class="abs slide-cta">Contact Us to Get Started</div>
<div class="abs slide-dots"><span class="on"></span><span></span><span></span><span></span></div>

<section class="abs welcome">
  <h1>Welcome to Our Website</h1>
  <p>Mossy Harbor Digital Marketing was founded in 2011 by Walt Perrin. After spending a couple years working in his dad’s insurance agency, he began to notice that lots of his dad’s clients were small business owners and needed an online presence. At this point, Walt learned as much as he could about building websites and this eventually led to him learning more about marketing on Chatterwall and Zorvic.</p>
</section>
<div class="abs divider"></div>

<h2 class="abs section-title products-title">Our Products</h2>
<div class="abs thumb" style="left:97px;top:656px"><div class="t1" role="img" aria-label="Businessman holding a tablet showing a rising campaign results chart"></div></div>
<div class="abs thumb" style="left:272px;top:656px"><div class="t2" role="img" aria-label="Hands holding a globe linked to web and social network icons"></div></div>
<div class="abs thumb" style="left:447px;top:656px"><div class="t3" role="img" aria-label="Word cloud of digital marketing, mobile, email and campaign terms"></div></div>
<div class="abs thumb" style="left:97px;top:758px"><div class="t4" role="img" aria-label="Customer icon at the centre of a network of social connections"></div></div>
<div class="abs thumb" style="left:272px;top:758px"><div class="t5" role="img" aria-label="Hand writing digital marketing, advertising and internet terms on a screen"></div></div>
<div class="abs thumb" style="left:447px;top:758px"><div class="t6" role="img" aria-label="Hand touching floating app and ad icons above a glowing screen"></div></div>

<h2 class="abs section-title offer-title">What We Offered</h2>
<ul class="abs offer-list">
  <li>Aliquam molestie, mi et</li>
  <li>Imperdiet euismod, dui purus</li>
  <li>Auctor tellus, et interdum</li>
  <li>Lacus lectus et ante. Sed</li>
  <li>Accumsan sollicitudin sapien,</li>
  <li>Sit amet adipiscing turpis</li>
  <li>Gravida ac In congue, neque</li>
  <li>Ac lobortis volutpat</li>
</ul>

<section class="abs panel rss">
  <div class="panel-head">
    <svg width="15" height="15" viewBox="0 0 16 16"><circle cx="3" cy="13" r="2.2" fill="#e8262b"/><path d="M1 7a8 8 0 0 1 8 8M1 2a13 13 0 0 1 13 13" stroke="#e8262b" stroke-width="2.4" fill="none"/></svg>
    RSS Feeds
  </div>
  <div class="rss-item">Aliquam ullamcorper tempor felis, nec condimentum...<div class="rss-date">Posted on 2 days ago</div></div>
  <div class="rss-item">Aliquam ullamcorper tempor felis, nec condimentum...<div class="rss-date">Posted on 2 days ago</div></div>
  <div class="rss-item">Aliquam ullamcorper tempor felis, nec condimentum...<div class="rss-date">Posted on 2 days ago</div></div>
  <div class="rss-more">READ ALL FEEDS</div>
</section>

<section class="abs panel vote">
  <div class="panel-head">
    <svg width="16" height="16" viewBox="0 0 16 16"><rect x="1" y="7" width="3" height="8" fill="#e8262b"/><path d="M5 7l4-6c1.5 0 2 1 1.6 2.4L10 6h4.2c1 0 1.6.9 1.3 1.8l-2 6.2c-.2.6-.8 1-1.4 1H5z" fill="#e8262b"/></svg>
    Vote Now
  </div>
  <div class="grant-badge" role="img" aria-label="Harbor Street Grants program badge"></div>
  <div class="vote-line vote-a">Help us get a</div>
  <div class="vote-line vote-b">$250K GRANT from Lanternbank.</div>
  <div class="vote-line vote-c">
    <svg width="18" height="16" viewBox="0 0 18 16"><rect x="1" y="3" width="12" height="12" fill="none" stroke="#1f63b5" stroke-width="1.6"/><path d="M4 8l3 3 9-10" stroke="#1f63b5" stroke-width="2.2" fill="none"/></svg>
    VOTE FOR US BEFORE NOV. 15
  </div>
  <div class="bank"><span></span>Lanternbank</div>
  <div class="vote-btn">VOTE NOW</div>
</section>

<section class="abs panel cert cert-a">
  <div class="cert-badge" role="img" aria-label="Qualified individual certification badge"></div>
  <div><h3>Zorvic BidLinks</h3><p>Put your ads directly where your clients will see them on the World’s largest search engine.</p></div>
</section>
<section class="abs panel cert cert-b">
  <div class="cert-badge" role="img" aria-label="Qualified individual certification badge"></div>
  <div><h3>Zorvic Insights</h3><p>Find out how people are using your site and the different ways people find your site online.</p></div>
</section>

<footer class="abs site-footer"></footer>
<div class="abs copyright">Copyright ©2013 - Mossy Harbor, Inc<br>All Right Reserved</div>
<div class="abs badge-a" role="img" aria-label="Partner badge"></div>
<div class="abs badge-b" role="img" aria-label="Accredited business badge"></div>

</body>
</html>
```